Corinnehabbard.com

1. Conceptualization and designing of the site Homepage. The Homepage design will be completely customized and based on your design instructions (i.e. preferred colors, links to reference sites that you want us to take reference from if any etc) and the recently completed logo design.
2. Upon homepage design approval, based on it we will be creating the layout for the other 4 site inner pages (i.e. About page, Contact page, Services page, and Insights (publications, media).
3. Once all the inner page designs are approved, we will get the designs built (will make sure that the site is completely Responsive - works on all devices) within your provided WIX account.
4. We will add the static text and images provided by you to the Home page, About page, Contact page, and the Services page. For the 2 Insights sub-pages, we will add 1-2 sample Publications and Media entries.
once you confirm the total number of required entries for the 2 sub-pages, I will accordingly quote you on the same
5. Integration of a Contact form on the Contact page that will email the filled in details to your mail id.

```html
<!DOCTYPE html>
<html lang="en">
<head>
<meta charset="utf-8">
<title>Corinne Habbard Consulting</title>
<link rel="stylesheet" href="https://fonts.googleapis.com/css2?family=Josefin+Sans:wght@400;600;700&family=Roboto:wght@400;500;700&display=swap">
<style>
:root{
  --green:#1e9a45;
  --green-light:#3fc15a;
  --orange:#f39200;
  --red:#e3101a;
  --ink:#111111;
  --body:#3a3a3a;
  --white:#ffffff;
  --sky:#7ac8ea;
  --black:#000000;
  --head:"Josefin Sans", sans-serif;
  --text:"Roboto", sans-serif;
}
*{margin:0;padding:0;box-sizing:border-box}
html,body{width:1200px;height:4380px;overflow:hidden;background:var(--white)}
body{position:relative;font-family:var(--text);color:var(--ink)}
a{text-decoration:none}
.abs{position:absolute}
.ph{position:absolute}

/* header */
.site-header{position:absolute;left:0;top:0;width:1200px;height:136px;background:var(--white)}
.brand{position:absolute;left:112px;top:18px;width:190px;text-align:center}
.brand-dot{width:64px;height:64px;border-radius:50%;border:3px solid var(--green);margin:0 auto 6px}
.brand-name{font-family:var(--head);font-weight:700;color:var(--green);font-size:16px;line-height:17px;letter-spacing:.5px}
.topinfo{position:absolute;top:14px;display:flex;align-items:center;gap:10px}
.topinfo .ic{width:42px;height:42px;border-radius:50%;border:2px solid #333;display:flex;align-items:center;justify-content:center}
.topinfo b{display:block;font-family:var(--head);color:var(--green);font-size:20px;font-weight:600}
.topinfo span{font-size:15px;color:var(--ink)}
.mainnav{position:absolute;left:328px;top:78px;width:872px;height:75px;background:var(--orange)}
.mainnav a{color:var(--white);font-weight:500;font-size:16px;position:absolute;top:28px}
.mainnav .active{background:var(--green);left:0;top:0;width:117px;height:75px;display:flex;align-items:center;justify-content:center}

/* hero */
.hero{position:absolute;left:0;top:136px;width:1200px;height:644px;background:linear-gradient(100deg,#3b3b3b 0%,#585858 45%,#6b6b6b 70%,#4a4a4a 100%)}
.hero-portrait{left:620px;top:0;width:580px;height:644px;background:radial-gradient(ellipse at 55% 45%,#a8785e 0%,#6b4532 35%,#2a1c16 70%,#1a1a1a 100%)}
.hero-welcome{left:112px;top:142px;font-family:var(--head);color:var(--white);font-size:37px;letter-spacing:3px}
.hero-title{left:108px;top:186px;font-family:var(--head);font-weight:700;color:var(--white);font-size:110px;line-height:100px;letter-spacing:4px}
.hero-sub{left:110px;top:390px;font-family:var(--head);font-weight:700;color:var(--green-light);font-size:44px;letter-spacing:3px}
.btn{display:inline-flex;align-items:center;justify-content:center;background:var(--red);color:var(--white);font-weight:700;font-size:17px;border-radius:30px;letter-spacing:.5px;text-decoration:none}
.hero .btn{position:absolute;left:112px;top:445px;width:148px;height:43px}

/* about */
.about-photo-a{left:112px;top:880px;width:338px;height:510px;background:linear-gradient(180deg,#e9e3d6 0%,#8a4f30 45%,#5a2c1a 75%,#3a2a24 100%)}
.about-photo-b{left:292px;top:1078px;width:233px;height:314px;background:linear-gradient(160deg,#cdd3da 0%,#8a7f78 50%,#2d3442 100%);border:8px solid var(--white)}
.badge{left:82px;top:1273px;width:146px;height:146px;border-radius:50%;background:var(--red);color:var(--white);text-align:center;padding-top:28px}
.badge b{display:block;font-family:var(--head);font-size:56px;line-height:56px}
.badge span{font-size:14px}
.label{font-family:var(--head);font-size:21px;display:flex;align-items:center;gap:6px}
.label i{width:22px;height:22px;border-radius:50%;border:2px solid currentColor;display:inline-block}
.heading{font-family:var(--head);font-weight:700;font-size:35px;line-height:43px}
.about .label{position:absolute;left:595px;top:884px;color:#2a8fd6}
.about .heading{position:absolute;left:595px;top:915px}
.about p{position:absolute;left:597px;width:487px;font-size:15px;line-height:28.5px;color:var(--body);text-align:justify}
.about .btn{position:absolute;left:597px;top:1317px;width:150px;height:42px}

/* services */
.services{position:absolute;left:0;top:1491px;width:1200px;height:1006px;background:linear-gradient(135deg,#86c598 0%,#7abd8d 40%,#86c598 60%,#79bb8b 100%)}
.services .label{position:absolute;left:131px;top:53px;color:var(--white)}
.services .heading{position:absolute;left:131px;top:90px;color:var(--white)}
.viewmore{position:absolute;left:991px;top:79px;width:96px;height:96px;border:3px solid var(--white);border-radius:50%;color:var(--white);font-family:var(--head);font-size:19px;text-align:center;padding-top:24px;line-height:22px;text-decoration:none}
.svc{position:absolute;top:234px;width:472px;height:667px;background:var(--white)}
.svc .icon{position:absolute;left:33px;top:35px;width:90px;height:90px;border-radius:50%;background:var(--orange)}
.svc h3{position:absolute;left:33px;top:142px;font-family:var(--head);font-weight:600;font-size:23px;letter-spacing:.5px}
.svc p{position:absolute;left:33px;top:178px;width:400px;font-size:14.5px;line-height:23px;color:var(--body)}
.more{color:var(--red);font-weight:700;font-size:15px;text-decoration:underline;font-family:var(--head)}
.svc .more{position:absolute;left:33px;top:257px}
.svc .ph{left:0;top:334px;width:472px;height:333px}

/* insights */
.insights .label{position:absolute;left:131px;top:2593px;color:#2a8fd6}
.insights .heading{position:absolute;left:131px;top:2627px}
.arrow{position:absolute;top:2630px;width:48px;height:48px;border-radius:50%;display:flex;align-items:center;justify-content:center}
.card{position:absolute;top:2762px;width:298px;height:420px;background:var(--white);box-shadow:0 2px 8px rgba(0,0,0,.18);text-align:center}
.card .ph{left:0;top:0;width:298px;height:264px}
.card h4{position:absolute;left:0;top:303px;width:298px;font-family:var(--head);font-weight:700;font-size:17px;line-height:26px}
.card .more{position:absolute;left:0;top:361px;width:298px}

/* contact */
.contact{position:absolute;left:0;top:3279px;width:1200px;height:682px;background:var(--sky)}
.contact .label{position:absolute;left:0;top:53px;width:1200px;justify-content:center;color:var(--white)}
.contact .heading{position:absolute;left:0;top:89px;width:1200px;text-align:center;color:var(--white);font-size:36px;line-height:42px}
.field{position:absolute;background:var(--white);font-family:var(--head);font-size:15px;color:#333;padding:20px 0 0 24px}

/* footer */
.site-footer{position:absolute;left:0;top:3961px;width:1200px;height:419px;background:var(--black);color:var(--white)}
.foot-brand{position:absolute;left:270px;top:60px;width:260px;text-align:center}
.foot-brand .dot{width:82px;height:82px;border-radius:50%;border:3px solid var(--white);margin:0 auto 8px}
.foot-brand b{font-family:var(--head);font-weight:600;font-size:21px;line-height:22px;letter-spacing:1px}
.news-title{position:absolute;left:571px;top:80px;font-family:var(--head);font-weight:600;font-size:22px}
.news-input{position:absolute;left:571px;top:124px;width:176px;height:42px;border:1px solid #aaa;font-family:var(--head);font-size:14px;padding:12px 0 0 10px}
.site-footer .btn{position:absolute;left:768px;top:124px;width:149px;height:42px}
.foot-nav a{position:absolute;top:212px;color:var(--white);font-size:16px}
.foot-info{position:absolute;top:270px;display:flex;align-items:center;gap:8px}
.foot-info .ic{width:44px;height:44px;border-radius:50%;border:2px solid var(--white);display:flex;align-items:center;justify-content:center}
.foot-info b{display:block;font-size:19px;font-weight:500}
.foot-info span{font-size:15px}
.copy{position:absolute;left:0;top:357px;width:1200px;text-align:center;font-size:15px}
</style>
</head>
<body>

<header class="site-header">
  <div class="brand">
    <div class="brand-dot"></div>
    <div class="brand-name">CORINNE HABBARD<br>CONSULTING</div>
  </div>
  <div class="topinfo" style="left:344px">
    <div class="ic"><svg width="20" height="20" viewBox="0 0 24 24"><path d="M6.6 10.8a15 15 0 006.6 6.6l2.2-2.2a1 1 0 011-.25 11 11 0 003.6.6 1 1 0 011 1V20a1 1 0 01-1 1A17 17 0 013 4a1 1 0 011-1h3.5a1 1 0 011 1 11 11 0 00.6 3.6 1 1 0 01-.25 1z" fill="#1e9a45"/></svg></div>
    <div><b>Phone No:</b><span>+1(555) 214 7730</span></div>
  </div>
  <div class="topinfo" style="left:570px">
    <div class="ic"><svg width="20" height="16" viewBox="0 0 24 18"><rect x="1" y="1" width="22" height="16" rx="2" fill="#1e9a45"/><path d="M2 3l10 7 10-7" stroke="#fff" stroke-width="2" fill="none"/></svg></div>
    <div><b>Email:</b><span>info@corinnehabbard.com</span></div>
  </div>
  <div class="topinfo" style="left:862px">
    <div class="ic"><svg width="18" height="22" viewBox="0 0 24 30"><path d="M12 1a10 10 0 00-10 10c0 8 10 18 10 18s10-10 10-18A10 10 0 0012 1z" fill="none" stroke="#1e9a45" stroke-width="3"/><circle cx="12" cy="11" r="3.5" fill="#1e9a45"/></svg></div>
    <div><b>Location:</b><span>Lorem ipsum dolor,USA</span></div>
  </div>
  <nav class="mainnav">
    <a class="active" href="#">HOME</a>
    <a href="#" style="left:163px">ABOUT US</a>
    <a href="#" style="left:331px">INSIGHTS</a>
    <a href="#" style="left:494px">SERVICES</a>
    <a href="#" style="left:660px">CONTACT US</a>
  </nav>
</header>

<section class="hero">
  <div class="ph hero-portrait" role="img" aria-label="Portrait of the consultant, office background"></div>
  <div class="abs hero-welcome">WELCOME TO</div>
  <h1 class="abs hero-title">CORINNE<br>HABBARD</h1>
  <div class="abs hero-sub">CONSULTING</div>
  <a class="btn" href="#">GET STARTED</a>
</section>

<section class="about">
  <div class="ph about-photo-a" role="img" aria-label="Consultant standing in front of a wooden office door"></div>
  <div class="ph about-photo-b" role="img" aria-label="Two colleagues reviewing documents together"></div>
  <div class="abs badge"><b>25+</b><span>Years Experience</span></div>
  <div class="label">About Us <i></i></div>
  <h2 class="heading">Lorem Ipsum Dolor Sit Amet,<br>Consectetur Elit</h2>
  <p style="top:1035px">Lorem ipsum dolor sit amet, consectetur adipiscing elit, sed do mod tempor incididunt ut labore et dolore magna liqua.isumuspendisse ultrices gravida. Risus commodo viverra ecenas accumsan lacus vel facilisis. Lorem ipsum dolor sit amet, consectetur adipiscing elit, sed do mod tempor incididunt ut labore et dolore agnaisumuspendisse ultrices gravida. Risus commodo viverra ecenas accumsan lacus vel facilisis.</p>
  <p style="top:1217px">Lorem ipsum dolor sit amet, consectetur adipiscing elit, sed do mod tempor incididunt ut labore et dolore magna liqua.isumuspendisse ultrices gravida.</p>
  <a class="btn" href="#">READ MORE</a>
</section>

<section class="services">
  <div class="label">Services <i></i></div>
  <h2 class="heading">Lorem Ipsum Dolor Sit Amet,<br>Consectetur Elit</h2>
  <a class="viewmore" href="#">VIEW<br>MORE</a>
  <article class="svc" style="left:112px">
    <div class="icon"></div>
    <h3>TRAINING OF REGISTERED NURSES</h3>
    <p>Lorem ipsum dolor sit amet, sectetur adipiscing elit, sed do eiusmod empor aliqua. sectetur adipiscing elit, sed do eiusmod empor aliqua.</p>
    <a class="more" href="#">READ MORE</a>
    <div class="ph" role="img" aria-label="Nurses and trainers seated in a training circle" style="background:linear-gradient(180deg,#d9dcd8 0%,#6f8d9c 45%,#3c4f60 100%)"></div>
  </article>
  <article class="svc" style="left:619px">
    <div class="icon"></div>
    <h3>CONSULTING FIRM</h3>
    <p>Lorem ipsum dolor sit amet, sectetur adipiscing elit, sed do eiusmod empor aliqua. sectetur adipiscing elit, sed do eiusmod empor aliqua.</p>
    <a class="more" href="#">READ MORE</a>
    <div class="ph" role="img" aria-label="Business people over a city skyline in blue tones" style="background:linear-gradient(180deg,#e8eef7 0%,#a9b8d3 50%,#3d4e76 100%)"></div>
  </article>
</section>

<section class="insights">
  <div class="label">Insights <i></i></div>
  <h2 class="heading">Lorem Ipsum Dolor Sit Amet,<br>Consectetur Elit</h2>
  <div class="arrow" style="left:972px;background:var(--red)"><svg width="20" height="20" viewBox="0 0 20 20"><path d="M17 10H4M9 4l-6 6 6 6" stroke="#fff" stroke-width="2" fill="none"/></svg></div>
  <div class="arrow" style="left:1040px;border:2px solid var(--red)"><svg width="20" height="20" viewBox="0 0 20 20"><path d="M3 10h13M11 4l6 6-6 6" stroke="#222" stroke-width="2" fill="none"/></svg></div>
  <article class="card" style="left:112px">
    <div class="ph" role="img" aria-label="Team meeting around a table with charts" style="background:linear-gradient(180deg,#e7ecef 0%,#9aa6b1 55%,#4d5866 100%)"></div>
    <h4>LOREM IPSUM DOLOR SIT<br>AMET, CONSECTETUR</h4>
    <a class="more" href="#">READ MORE</a>
  </article>
  <article class="card" style="left:450px">
    <div class="ph" role="img" aria-label="Colleagues discussing at a conference table" style="background:linear-gradient(180deg,#ececea 0%,#a3958a 55%,#5a4a40 100%)"></div>
    <h4>LOREM IPSUM DOLOR SIT<br>AMET, CONSECTETUR</h4>
    <a class="more" href="#">READ MORE</a>
  </article>
  <article class="card" style="left:787px">
    <div class="ph" role="img" aria-label="Two professionals working on a laptop" style="background:linear-gradient(180deg,#c9d6dd 0%,#8f9aa5 50%,#2e3442 100%)"></div>
    <h4>LOREM IPSUM DOLOR SIT<br>AMET, CONSECTETUR</h4>
    <a class="more" href="#">READ MORE</a>
  </article>
</section>

<section class="contact">
  <div class="label">Contact Us <i></i></div>
  <h2 class="heading">Lorem Ipsum Dolor Sit Amet,<br>Consectetur Elit</h2>
  <div class="field" style="left:129px;top:203px;width:473px;height:61px">First Name</div>
  <div class="field" style="left:631px;top:203px;width:459px;height:61px">Last Name</div>
  <div class="field" style="left:129px;top:279px;width:473px;height:61px">Email Address</div>
  <div class="field" style="left:631px;top:279px;width:459px;height:61px">Phone No</div>
  <div class="field" style="left:129px;top:357px;width:961px;height:199px">Message Here...</div>
  <a class="btn" href="#" style="position:absolute;left:525px;top:580px;width:150px;height:42px">SUBMIT NOW</a>
</section>

<footer class="site-footer">
  <div class="foot-brand"><div class="dot"></div><b>CORINNE HABBARD<br>CONSULTING</b></div>
  <div class="news-title">Subscribe To Our Newsletter</div>
  <div class="news-input">Email</div>
  <a class="btn" href="#">SUBSCRIBE</a>
  <nav class="foot-nav">
    <a href="#" style="left:236px">HOME</a>
    <a href="#" style="left:370px">ABOUT US</a>
    <a href="#" style="left:535px">INSIGHTS</a>
    <a href="#" style="left:697px">SERVICES</a>
    <a href="#" style="left:858px">CONTACT US</a>
  </nav>
  <div class="foot-info" style="left:236px">
    <div class="ic"><svg width="20" height="20" viewBox="0 0 24 24"><path d="M6.6 10.8a15 15 0 006.6 6.6l2.2-2.2a1 1 0 011-.25 11 11 0 003.6.6 1 1 0 011 1V20a1 1 0 01-1 1A17 17 0 013 4a1 1 0 011-1h3.5a1 1 0 011 1 11 11 0 00.6 3.6 1 1 0 01-.25 1z" fill="#fff"/></svg></div>
    <div><b>Phone No:</b><span>+1(555) 214 7730</span></div>
  </div>
  <div class="foot-info" style="left:464px">
    <div class="ic"><svg width="20" height="16" viewBox="0 0 24 18"><rect x="1" y="1" width="22" height="16" rx="2" fill="#fff"/><path d="M2 3l10 7 10-7" stroke="#000" stroke-width="2" fill="none"/></svg></div>
    <div><b>Email:</b><span>info@corinnehabbard.com</span></div>
  </div>
  <div class="foot-info" style="left:753px">
    <div class="ic"><svg width="18" height="22" viewBox="0 0 24 30"><path d="M12 1a10 10 0 00-10 10c0 8 10 18 10 18s10-10 10-18A10 10 0 0012 1z" fill="none" stroke="#fff" stroke-width="3"/><circle cx="12" cy="11" r="3.5" fill="#fff"/></svg></div>
    <div><b>Location:</b><span>Lorem ipsum dolor,USA</span></div>
  </div>
  <div class="copy">Copyright © 2024 Corinne Habbard Consulting | All Rights Reserved</div>
</footer>

</body>
</html>
```